BRIGHT RIVER POWER.

I'd like my business logo.
contact name: Dennis Halvorsen
phone:0438759164
email: info@brightriverpower.net.au
website: www.brightriverpower.net.au

services:
solar
battery storage
LED lighting
energy saving solutions
general electrical
I'd like the design to look professional

Target Market(s)

Everyone

Industry/Entity Type

Business

Contact Information for Business Card

as described above

Requirements
Must have
• Id like the colours and the design to work well with my logo.

```html
<!DOCTYPE html>
<html lang="en">
<head>
<meta charset="utf-8">
<title>Bright River Power – Business Card</title>
<link rel="stylesheet" href="https://fonts.googleapis.com/css2?family=Open+Sans:wght@400;600;700&display=swap">
<style>
  :root {
    --backdrop: #2e2926;
    --card-white: #fbfbf9;
    --card-black: #1b1b1b;
    --ink: #2a2a2a;
    --orange: #f29a16;
    --green: #7cc242;
    --green-dark: #3f9c35;
  }
  * { box-sizing: border-box; margin: 0; padding: 0; }
  html, body {
    width: 1200px; height: 844px; overflow: hidden;
    background: var(--backdrop);
    font-family: "Open Sans", Arial, sans-serif;
  }
  .stage {
    position: relative; width: 1200px; height: 844px;
    display: flex; align-items: center; justify-content: center; gap: 60px;
  }
  .card {
    position: relative; width: 500px; height: 286px;
    box-shadow: 0 10px 30px rgba(0,0,0,.45);
  }
  .card--front { background: var(--card-white); color: var(--ink); }
  .card--back { background: var(--card-black); }

  .brand {
    position: absolute; top: 48px; right: 48px;
    display: flex; align-items: center; gap: 10px;
  }
  .brand__dot { width: 22px; height: 22px; border-radius: 50%; background: var(--orange); }
  .brand__name {
    font-weight: 700; font-size: 24px; letter-spacing: .5px; color: var(--green-dark);
  }

  .contact { position: absolute; left: 40px; bottom: 40px; }
  .contact__name {
    font-weight: 600; font-size: 19px; color: var(--orange); margin-bottom: 16px;
  }
  .contact__list { list-style: none; }
  .contact__item {
    display: flex; align-items: center; gap: 12px;
    font-size: 15px; line-height: 27px; color: var(--ink);
  }
  .contact__icon { width: 13px; height: 13px; flex: none; }

  .back__mark {
    position: absolute; top: 28px; right: 30px;
    display: flex; align-items: center; gap: 8px;
  }
  .back__mark .brand__dot { width: 16px; height: 16px; }
  .back__mark .brand__name { font-size: 15px; color: var(--green); }

  .services { position: absolute; left: 40px; top: 112px; }
  .services__title {
    font-weight: 700; font-size: 22px; color: var(--orange); margin-bottom: 12px;
  }
  .services__list { list-style: none; }
  .services__item {
    display: flex; align-items: center; gap: 10px;
    font-size: 14px; line-height: 22px; color: var(--green);
  }
  .services__tick { width: 12px; height: 12px; flex: none; }
</style>
</head>
<body>
<main class="stage">

  <section class="card card--front" aria-label="Business card front">
    <div class="brand">
      <span class="brand__dot"></span>
      <span class="brand__name">BRIGHT RIVER POWER</span>
    </div>
    <div class="contact">
      <p class="contact__name">Dennis Halvorsen</p>
      <ul class="contact__list">
        <li class="contact__item">
          <svg class="contact__icon" viewBox="0 0 16 16" aria-hidden="true"><path fill="#f29a16" d="M3.5 1.5l2.5 0 1 3.5-1.6 1.2c.8 1.8 2.2 3.2 4 4L10.6 8.6l3.5 1v2.5c0 .8-.7 1.5-1.5 1.5C7 13.6 2 8.6 2 3c0-.8.7-1.5 1.5-1.5z"/></svg>
          0438759164
        </li>
        <li class="contact__item">
          <svg class="contact__icon" viewBox="0 0 16 16" aria-hidden="true"><rect x="1" y="3" width="14" height="10" rx="1" fill="#f29a16"/><path d="M1.5 3.8L8 9l6.5-5.2" fill="none" stroke="#fff" stroke-width="1.3"/></svg>
          info@brightriverpower.net.au
        </li>
        <li class="contact__item">
          <svg class="contact__icon" viewBox="0 0 16 16" aria-hidden="true"><circle cx="8" cy="8" r="7" fill="#f29a16"/><path d="M1 8h14M8 1c-2.5 3-2.5 11 0 14M8 1c2.5 3 2.5 11 0 14" fill="none" stroke="#fff" stroke-width="1"/></svg>
          www.brightriverpower.net.au
        </li>
      </ul>
    </div>
  </section>

  <section class="card card--back" aria-label="Business card back">
    <div class="back__mark">
      <span class="brand__dot"></span>
      <span class="brand__name">BRIGHT RIVER POWER</span>
    </div>
    <div class="services">
      <h2 class="services__title">What I do</h2>
      <ul class="services__list">
        <li class="services__item"><svg class="services__tick" viewBox="0 0 12 12" aria-hidden="true"><circle cx="6" cy="6" r="6" fill="#7cc242"/><path d="M3 6.2l2 2 4-4.2" fill="none" stroke="#1b1b1b" stroke-width="1.5"/></svg>Solar</li>
        <li class="services__item"><svg class="services__tick" viewBox="0 0 12 12" aria-hidden="true"><circle cx="6" cy="6" r="6" fill="#7cc242"/><path d="M3 6.2l2 2 4-4.2" fill="none" stroke="#1b1b1b" stroke-width="1.5"/></svg>Battery Storage</li>
        <li class="services__item"><svg class="services__tick" viewBox="0 0 12 12" aria-hidden="true"><circle cx="6" cy="6" r="6" fill="#7cc242"/><path d="M3 6.2l2 2 4-4.2" fill="none" stroke="#1b1b1b" stroke-width="1.5"/></svg>LED Lighting</li>
        <li class="services__item"><svg class="services__tick" viewBox="0 0 12 12" aria-hidden="true"><circle cx="6" cy="6" r="6" fill="#7cc242"/><path d="M3 6.2l2 2 4-4.2" fill="none" stroke="#1b1b1b" stroke-width="1.5"/></svg>Energy Saving Solutions</li>
      </ul>
    </div>
  </section>

</main>
</body>
</html>
```